Corvanth Veylor - Advanced Skincare and undetectable Makeup for Men

We are in need of a professional webpage for our company Corvanth Veylor. We help every man feel his best by looking his best. Inspired by the myth of Corvanth, we offer makeup and skincare products along with education upon their use. Our mission is to celebrate masculinity in all of its forms, regardless of age, race, sexual orientation, or assigned gender at birth.

The webpage would serve as our online store, as a place where our clients can learn about our brand, view our "How-to" video tutorials, and get product information. An online blog will also be hosted in order to keep clients up to date with news, updates, media mentions, etc.

The color schemes that we use are mostly Black and Gold, with Red accents. please keep in mind that this is a men's cosmetics line, and therefore should read powerful, sexy, confident and bold - all with a high end look and feel.

Think along the lines of brands like Lem Brisko, QDV, Belluti, etc.

our logo is included in the files attached. images and copy will be added in at a later time; hence, general images that fit the feel and filler text is encouraged.

The products to be sold include:
a face cleanser in a pump dispenser bottle (1 size)
a mask in a round jar container (1 size)
a moisturizer in a pump container 1 size)
a concealer in a click pen with a brush applicator (3 shades)
a liquid liner pen (4 shades)
a contouring palette (2 shade options)
a setting spray (single option)

Target Market(s)

Millennial Men

Industry/Entity Type

Beauty

Number of Pages Required

5+ page

Font styles to use
Serif

Colors
ec1f27
000000
faa54b

Requirements
Must have
• ur essential requirements are:
• 1) a stunning and engaging landing page that truly captures the ideals of sexuality, boldness and confidence.
• 2) an interactive and engaging online store that is easy to update / add product / information to.
• 3) Product pages supporting various toggling images of the product, a shade selection option, ingredient information, usage instructions, pricing, and a link to a "how to video" unique to each individual product.
• 4) dedicated space where all of the tutorials can be organized together
• 5) an organized Blog section, that would include a segment for a Q&A section for us to update as the brand grows, ongoing contests (that would be easily hidden if there are no contests running at the moment) as well as general news and updates segment.
• 6) an "about us" page, where our customers are able to learn about our story, inspirations, humanitarian efforts and philosophies in product contents and purity.
• 7) a contact us page, which would include social media links, contact email and telephone number as well as physical address to be updated upon launch.
• 8) discrete privacy policy, terms of use, and return policy links available at the bottom of every page
Nice to have
• 1) A posting forum where clients could post their looks using our products, or maybe a live stream of our Pictoval account.
• 2) a member sign in page so that we can collect and store customer information for faster check out, keep track of purchases attached to their email address (future loyalty program plans) and maintain an email database for email notifications and the such.

```html
<!DOCTYPE html>
<html lang="en">
<head>
<meta charset="utf-8">
<title>Corvanth Veylor</title>
<link rel="stylesheet" href="https://fonts.googleapis.com/css2?family=Cinzel:wght@400;600&family=Poppins:wght@400;500;600;700&display=swap">
<style>
:root{
  --black:#000;
  --ink:#0b0b0d;
  --gold:#faa54b;
  --yellow:#fdb515;
  --red:#ec1f27;
  --white:#fff;
  --grey:#f1f1f1;
  --band:rgba(20,20,22,.82);
}
*{margin:0;padding:0;box-sizing:border-box}
html,body{width:1200px;height:3750px;overflow:hidden;background:var(--black)}
body{position:relative;font-family:"Poppins",Arial,sans-serif;color:var(--white)}
.abs{position:absolute}
.btn{position:absolute;display:flex;align-items:center;justify-content:center;font-size:13px;font-weight:600;letter-spacing:.3px}
.btn-red{background:var(--red);color:var(--white)}
.btn-yellow{background:var(--yellow);color:var(--white)}
.btn-outline{border:2px solid var(--white);color:var(--white)}

/* header + hero */
.hero{left:0;top:0;width:1200px;height:610px;background:
  radial-gradient(ellipse 60% 80% at 72% 55%,#1c1026 0%,rgba(12,7,18,0) 70%),
  linear-gradient(90deg,#231a1d 0%,#17101a 40%,#0c0712 100%)}
.hero-photo{left:130px;top:70px;width:480px;height:540px;background:
  radial-gradient(ellipse 26% 22% at 52% 24%,#e3b9a6 0%,#c28f7c 45%,rgba(150,100,90,0) 100%),
  radial-gradient(ellipse 22% 30% at 40% 30%,#3a2420 0%,rgba(40,25,22,0) 100%),
  radial-gradient(ellipse 34% 20% at 50% 48%,#d5a896 0%,rgba(180,130,115,0) 100%),
  radial-gradient(ellipse 60% 45% at 50% 85%,#1a1416 0%,#0f0b0e 60%,rgba(15,10,14,0) 100%),
  linear-gradient(180deg,rgba(30,20,24,0) 0%,rgba(20,14,18,.6) 100%)}
.site-header{left:0;top:0;width:1200px;height:70px;background:var(--black)}
.logo-box{left:100px;top:0;width:150px;height:110px;background:var(--black);display:flex;flex-direction:column;align-items:center;justify-content:center;gap:8px}
.logo-mark{width:26px;height:26px;background:var(--gold)}
.logo-name{font-family:"Cinzel",Georgia,serif;font-size:10px;letter-spacing:1.5px;color:var(--gold)}
.nav{left:308px;top:0;height:78px;display:flex;align-items:center;font-size:12.5px;font-weight:500}
.nav a{color:var(--white);text-decoration:none;margin-right:38px}
.nav a.active{color:var(--red)}
.search{left:852px;top:26px;width:150px;height:24px;border-bottom:1px solid var(--white);font-size:9px;display:flex;justify-content:space-between;align-items:center}
.cart{left:1040px;top:0;width:160px;height:70px;background:var(--yellow);border-bottom-left-radius:45px}
.hero-title{left:618px;top:228px;font-family:"Cinzel",Georgia,serif;font-size:50px;letter-spacing:2px;font-weight:400}
.hero-sub{left:618px;top:316px;font-size:14.5px}
.dots{left:618px;top:458px;display:flex;gap:12px}
.dots span{width:8px;height:8px;border-radius:50%;background:var(--white)}
.dots span:first-child{background:var(--yellow)}

/* products */
.tile{position:absolute;overflow:hidden}
.tile .photo{position:absolute;inset:0}
.tile .cap{position:absolute;left:0;right:0;bottom:0;background:var(--band);font-weight:600}
.p-cleanser{left:0;top:610px;width:522px;height:365px}
.p-mask{left:522px;top:610px;width:340px;height:365px}
.p-moist{left:862px;top:610px;width:338px;height:365px}
.row2{top:975px;width:300px;height:322px}

/* about */
.section-title{position:absolute;font-weight:700;font-size:35px}
.rule{position:absolute;width:40px;height:4px}
.about-text{left:100px;top:1500px;width:450px;font-size:11.5px;line-height:31px;color:#e6e6e6}
.about-frame{left:602px;top:1388px;width:490px;height:394px;border:2px solid var(--yellow)}
.about-photo{left:612px;top:1400px;width:488px;height:390px;background:
  radial-gradient(ellipse 30% 40% at 72% 42%,#e7c3ae 0%,#d1a58e 50%,rgba(200,160,140,0) 100%),
  radial-gradient(ellipse 16% 20% at 22% 55%,#2a2a2c 0%,#6a6a6e 55%,rgba(120,120,125,0) 100%),
  radial-gradient(ellipse 25% 30% at 30% 85%,#e4b9a3 0%,rgba(220,180,160,0) 100%),
  linear-gradient(135deg,#eef0f3 0%,#dcdde2 45%,#b9a6a0 100%)}

/* blog */
.blog{left:0;top:1887px;width:1200px;height:668px;background:var(--yellow)}
.card{position:absolute;top:2102px;width:315px;height:350px;background:var(--ink)}
.card .photo{height:200px}
.card h3{position:absolute;left:16px;top:232px;font-size:15px;font-weight:600;color:var(--yellow)}
.card p{position:absolute;left:16px;top:262px;font-size:11.5px;color:#ddd}
.card .meta{position:absolute;left:16px;top:320px;font-size:9.5px;color:var(--red)}
.arrow{position:absolute;top:2262px;width:32px;height:32px;border-radius:50%;background:var(--white);display:flex;align-items:center;justify-content:center}

/* video */
.video-card{left:100px;top:2790px;width:618px;height:375px;background:var(--grey);border-radius:40px}
.video-card h3{position:absolute;left:52px;top:52px;width:400px;font-size:17px;font-weight:600;line-height:30px;color:#222}
.video-card p{position:absolute;left:52px;top:132px;width:410px;font-size:12px;line-height:27px;color:#888}
.video-player{left:643px;top:2827px;width:457px;height:300px;border-radius:30px;overflow:hidden;background:
  radial-gradient(ellipse 22% 30% at 40% 40%,#f1d0c6 0%,#d9a7a3 60%,rgba(210,160,160,0) 100%),
  radial-gradient(ellipse 30% 45% at 85% 45%,#f4eeea 0%,rgba(240,230,226,0) 100%),
  linear-gradient(135deg,#dcaeb0 0%,#c48c92 55%,#a86c73 100%)}
.video-bar{position:absolute;left:0;right:0;bottom:0;height:48px;background:rgba(30,20,22,.85);font-size:12px;font-weight:600;display:flex;align-items:center;padding-left:40px}

/* newsletter */
.newsletter{left:0;top:3268px;width:1200px;height:107px;background:var(--yellow)}
.newsletter h4{position:absolute;left:100px;top:40px;font-size:19px;font-weight:700;color:#111}
.email-input{left:375px;top:34px;width:365px;height:40px;background:var(--white);color:#777;font-size:12px;display:flex;align-items:center;padding-left:22px}
.social{left:876px;top:42px;display:flex;gap:9px}
.social span{width:22px;height:22px;border-radius:50%;background:var(--white);display:flex;align-items:center;justify-content:center}
.social span::after{content:"";width:8px;height:8px;border-radius:2px;background:#111}

/* footer */
.map{left:0;top:3375px;width:1200px;height:375px;background:
  radial-gradient(ellipse 20% 30% at 20% 30%,#f2f2f0 0%,rgba(240,240,238,0) 100%),
  radial-gradient(ellipse 25% 25% at 45% 75%,#d6d8d4 0%,rgba(214,216,212,0) 100%),
  radial-gradient(ellipse 12% 20% at 95% 15%,#dfe6da 0%,rgba(220,230,215,0) 100%),
  linear-gradient(160deg,#e6e6e6 0%,#d4d6d8 50%,#e9e9e7 100%)}
.contact{left:675px;top:3375px;width:425px;height:375px;background:var(--black);text-align:center}
.contact h4{margin-top:30px;font-size:24px;font-weight:600}
.contact .line{font-size:13px;display:flex;align-items:center;justify-content:center;gap:12px}
</style>
</head>
<body>

<!-- hero -->
<div class="abs hero">
  <div class="abs hero-photo" role="img" aria-label="Portrait of a model with bold red lips in a dark lace top"></div>
</div>
<header class="abs site-header"></header>
<div class="abs logo-box"><span class="logo-mark"></span><span class="logo-name">CORVANTH VEYLOR</span></div>
<nav class="abs nav">
  <a class="active">HOME</a><a>PRODUCTS</a><a>VIDEO TUTORIALS</a><a>BLOG</a><a>CONTACT US</a>
</nav>
<div class="abs search"><span>SEARCH...</span>
  <svg width="10" height="10" viewBox="0 0 10 10"><circle cx="4" cy="4" r="3" fill="none" stroke="#fff" stroke-width="1.3"/><path d="M6.3 6.3L9 9" stroke="#fff" stroke-width="1.3"/></svg>
</div>
<div class="abs cart">
  <svg class="abs" style="left:20px;top:26px" width="34" height="28" viewBox="0 0 34 28"><path d="M2 3h5l4 15h16l4-11H9" fill="none" stroke="#000" stroke-width="2.5"/><circle cx="13" cy="24" r="2.5"/><circle cx="25" cy="24" r="2.5"/></svg>
  <span class="abs" style="left:48px;top:18px;width:18px;height:18px;border-radius:50%;background:var(--red);font-size:9px;display:flex;align-items:center;justify-content:center">0</span>
</div>
<h1 class="abs hero-title">CORVANTH VEYLOR</h1>
<p class="abs hero-sub">Sed ut perspiciatis unde omnis iste natus error sit voluccusantium.</p>
<span class="btn btn-red" style="left:618px;top:372px;width:117px;height:43px">SHOP NOW</span>
<span class="btn btn-outline" style="left:743px;top:372px;width:155px;height:43px">VIEW PRODUCTS</span>
<div class="abs dots"><span></span><span></span><span></span><span></span></div>

<!-- products -->
<div class="tile p-cleanser">
  <div class="photo" role="img" aria-label="Face cleanser pump bottle in use" style="background:
    radial-gradient(ellipse 22% 35% at 62% 35%,#e6c2ad 0%,#c99a84 55%,rgba(200,150,130,0) 100%),
    radial-gradient(ellipse 25% 45% at 80% 40%,#7a4e34 0%,rgba(120,80,55,0) 100%),
    radial-gradient(ellipse 10% 30% at 47% 55%,#f4f4f4 0%,rgba(240,240,240,0) 100%),
    linear-gradient(110deg,#2f3433 0%,#5f6863 35%,#a69a8e 70%,#d8c7b6 100%)"></div>
  <div class="cap" style="height:92px">
    <span class="abs" style="left:43px;top:20px;font-size:24px">Face cleanser</span>
    <span class="abs" style="left:43px;top:56px;font-size:14px;font-weight:400">(1 size)</span>
    <span class="btn btn-red" style="left:375px;top:18px;width:105px;height:40px">View Now</span>
  </div>
</div>
<div class="tile p-mask">
  <div class="photo" role="img" aria-label="Mask in an open round jar" style="background:
    radial-gradient(ellipse 40% 28% at 55% 35%,#ffffff 0%,#f1f1ef 60%,rgba(235,235,232,0) 100%),
    radial-gradient(ellipse 45% 40% at 50% 70%,#d9d8d3 0%,rgba(210,208,203,0) 100%),
    radial-gradient(ellipse 25% 30% at 10% 15%,#bfc7a8 0%,rgba(190,200,170,0) 100%),
    linear-gradient(160deg,#ecebe7 0%,#dedcd7 60%,#c4c2bc 100%)"></div>
  <div class="cap" style="height:92px"><span class="abs" style="left:31px;top:40px;font-size:18px">Mask</span></div>
</div>
<div class="tile p-moist">
  <div class="photo" role="img" aria-label="Moisturizer applied to the shoulder" style="background:
    radial-gradient(ellipse 45% 40% at 60% 55%,#efc6ae 0%,#e0a98d 55%,rgba(220,165,135,0) 100%),
    radial-gradient(ellipse 35% 30% at 15% 20%,#f7ece4 0%,rgba(245,235,228,0) 100%),
    linear-gradient(150deg,#f4e3d8 0%,#e6bda7 55%,#c88f74 100%)"></div>
  <div class="cap" style="height:92px"><span class="abs" style="left:35px;top:40px;font-size:18px">Moisturizer</span></div>
</div>

<div class="tile row2" style="left:0">
  <div class="photo" role="img" aria-label="Concealer bottles in several shades" style="background:
    radial-gradient(ellipse 14% 45% at 22% 65%,#f1d2b8 0%,#d9ac8a 60%,rgba(210,165,130,0) 100%),
    radial-gradient(ellipse 14% 45% at 55% 60%,#e8bb96 0%,#c18c68 60%,rgba(190,140,105,0) 100%),
    radial-gradient(ellipse 12% 18% at 58% 18%,#3a2a28 0%,rgba(58,42,40,0) 100%),
    linear-gradient(140deg,#f3e4d6 0%,#d7b9a0 55%,#8a6a58 100%)"></div>
  <div class="cap" style="height:85px"><span class="abs" style="left:32px;top:35px;font-size:14px">Concealer</span></div>
</div>
<div class="tile row2" style="left:300px">
  <div class="photo" role="img" aria-label="Liquid liner pens in a row" style="background:
    radial-gradient(ellipse 60% 18% at 50% 45%,#c8595a 0%,rgba(200,90,90,0) 100%),
    radial-gradient(ellipse 50% 20% at 40% 25%,#7dbfb3 0%,rgba(125,190,180,0) 100%),
    linear-gradient(160deg,#6a3a3e 0%,#b26a66 45%,#4b6b5a 100%)"></div>
  <div class="cap" style="height:85px"><span class="abs" style="left:35px;top:35px;font-size:14px">Liquid liner pen</span></div>
</div>
<div class="tile row2" style="left:600px">
  <div class="photo" role="img" aria-label="Contouring palette with brush" style="background:
    radial-gradient(ellipse 30% 15% at 30% 75%,#c48a6a 0%,rgba(190,135,105,0) 100%),
    radial-gradient(ellipse 30% 15% at 75% 75%,#8f5a44 0%,rgba(140,90,68,0) 100%),
    radial-gradient(ellipse 40% 20% at 50% 20%,#4a4a4e 0%,rgba(70,70,75,0) 100%),
    linear-gradient(170deg,#1f1f21 0%,#3b3433 50%,#5a4138 100%)"></div>
  <div class="cap" style="height:85px"><span class="abs" style="left:35px;top:35px;font-size:14px">Contouring palette</span></div>
</div>
<div class="tile row2" style="left:900px">
  <div class="photo" role="img" aria-label="Setting spray being applied to styled hair" style="background:
    radial-gradient(ellipse 35% 40% at 85% 30%,#e8d4ad 0%,#c9b188 55%,rgba(200,175,135,0) 100%),
    radial-gradient(ellipse 25% 30% at 30% 30%,#2a2a2a 0%,rgba(40,40,40,0) 100%),
    radial-gradient(ellipse 30% 20% at 55% 25%,#9c9893 0%,rgba(155,150,145,0) 100%),
    linear-gradient(140deg,#161616 0%,#4a4744 55%,#c9b9a0 100%)"></div>
  <div class="cap" style="height:85px"><span class="abs" style="left:32px;top:35px;font-size:14px">Setting spray</span></div>
</div>

<!-- about -->
<h2 class="section-title" style="left:100px;top:1403px;color:var(--yellow)">ABOUT US</h2>
<span class="rule" style="left:100px;top:1467px;background:var(--yellow)"></span>
<p class="abs about-text">Sed ut perspiciatis unde omnis iste natus error sit voluptatem accusantium doloremque laudantium, totam rem aperiam, eaque ipsa quae ab illo inventore veritatis et quasi architecto beatae vitae dicta sunt explicabo. Nemo enim ipsam voluptatem quia voluptas sit aspernatur aut odit aut fugit, sed quia consequuntur magni dolores eos qui ratione voluptatem sequi nesciunt. po qui dolorem ipsum quia dolor sit amet.</p>
<span class="btn btn-red" style="left:100px;top:1722px;width:115px;height:45px">READ MORE</span>
<div class="abs about-frame"></div>
<div class="abs about-photo" role="img" aria-label="Close-up of eye makeup being applied with a brush"></div>

<!-- blog -->
<section class="abs blog"></section>
<h2 class="section-title" style="left:0;width:1200px;text-align:center;top:1978px;color:#111">BLOG POSTS</h2>
<span class="rule" style="left:580px;top:2042px;background:#111"></span>
<article class="card" style="left:100px">
  <div class="photo" role="img" aria-label="Hair stylist at work in a salon" style="background:
    radial-gradient(ellipse 25% 40% at 25% 40%,#5a3226 0%,#8a5a48 55%,rgba(130,90,70,0) 100%),
    radial-gradient(ellipse 20% 30% at 30% 75%,#e0b9a2 0%,rgba(220,180,160,0) 100%),
    linear-gradient(120deg,#7a5a50 0%,#b8a6a2 45%,#e4e8ef 75%,#f4f4f6 100%)"></div>
  <h3>Sed ut perspiciatis unde..</h3><p>Lorem ipsum dolor sit amet, consectetur adip-</p><span class="meta">By Admin &nbsp;&nbsp; November 18, 2017</span>
</article>
<article class="card" style="left:443px">
  <div class="photo" role="img" aria-label="Hands holding a makeup compact and brush" style="background:
    radial-gradient(ellipse 18% 20% at 38% 55%,#2a2224 0%,#5a4a4a 60%,rgba(90,75,75,0) 100%),
    radial-gradient(ellipse 35% 40% at 70% 40%,#e7c0ac 0%,rgba(225,185,165,0) 100%),
    linear-gradient(135deg,#efe9e5 0%,#d7b9ab 55%,#a6807a 100%)"></div>
  <h3>Sed ut perspiciatis unde..</h3><p>Lorem ipsum dolor sit amet, consectetur adip-</p><span class="meta">By Admin &nbsp;&nbsp; November 18, 2017</span>
</article>
<article class="card" style="left:785px">
  <div class="photo" role="img" aria-label="Skincare bottles on a bright table" style="background:
    radial-gradient(ellipse 12% 35% at 35% 60%,#e9eddf 0%,#c9cfb8 60%,rgba(200,205,185,0) 100%),
    radial-gradient(ellipse 30% 25% at 45% 10%,#c9a898 0%,rgba(200,168,152,0) 100%),
    radial-gradient(ellipse 18% 10% at 75% 80%,#3a3a3c 0%,rgba(58,58,60,0) 100%),
    linear-gradient(170deg,#e8dfd5 0%,#ddd6cd 55%,#f2f0ec 100%)"></div>
  <h3>Sed ut perspiciatis unde..</h3><p>Lorem ipsum dolor sit amet, consectetur adip-</p><span class="meta">By Admin &nbsp;&nbsp; November 18, 2017</span>
</article>
<span class="arrow" style="left:38px"><svg width="10" height="12" viewBox="0 0 10 12"><path d="M7 1L2 6l5 5" fill="none" stroke="#fdb515" stroke-width="2"/></svg></span>
<span class="arrow" style="left:1128px"><svg width="10" height="12" viewBox="0 0 10 12"><path d="M3 1l5 5-5 5" fill="none" stroke="#fdb515" stroke-width="2"/></svg></span>

<!-- video tutorials -->
<h2 class="section-title" style="left:0;width:1200px;text-align:center;top:2643px;color:var(--yellow)">VIDEO TUTORIALS</h2>
<span class="rule" style="left:580px;top:2705px;background:var(--yellow)"></span>
<div class="abs video-card">
  <h3>Sed ut perspiciatis unde omnis iste natus error sit voluptatem..</h3>
  <p>Sed ut perspiciatis unde omnis iste natus error sit voluptatem accusantium doloremque laudantium totam rem aperiam ipsa quae ab illo iise vits modi tempora incidunt ut labore et dolore magnam aliquamse dicta sunt explicabo.</p>
  <span class="btn btn-red" style="left:52px;top:268px;width:110px;height:42px">Learn More</span>
  <span class="btn btn-yellow" style="left:175px;top:268px;width:110px;height:42px">Subscribe</span>
</div>
<div class="abs video-player" role="img" aria-label="Video still of a model applying makeup with a compact mirror">
  <svg class="abs" style="left:205px;top:125px" width="50" height="50" viewBox="0 0 50 50"><circle cx="25" cy="25" r="25" fill="#fff"/><path d="M20 16l14 9-14 9z" fill="#333"/></svg>
  <div class="video-bar">EIUS MODI TEMPO ,&nbsp;<span style="color:var(--yellow);font-weight:400;font-size:11px">Customer</span>
    <span class="abs" style="right:34px;top:21px;display:flex;gap:5px"><i style="width:5px;height:5px;border-radius:50%;background:var(--red)"></i><i style="width:5px;height:5px;border-radius:50%;background:#fff"></i><i style="width:5px;height:5px;border-radius:50%;background:#fff"></i><i style="width:5px;height:5px;border-radius:50%;background:#fff"></i></span>
  </div>
</div>

<!-- newsletter -->
<section class="abs newsletter">
  <h4>NEWSLETTER SIGNUP</h4>
  <div class="abs email-input">Enter Email</div>
  <span class="btn btn-red" style="left:740px;top:34px;width:112px;height:40px">SIGN UP</span>
  <div class="abs social" aria-label="Social links"><span></span><span></span><span></span><span></span><span></span><span></span><span></span><span></span></div>
</section>

<!-- footer -->
<div class="abs map" role="img" aria-label="Street map showing the store location"></div>
<footer class="abs contact">
  <h4>Contact Info</h4>
  <span class="abs" style="left:192px;top:80px;width:40px;height:4px;background:var(--yellow)"></span>
  <div class="abs" style="left:0;right:0;top:120px;display:flex;flex-direction:column;align-items:center;gap:12px">
    <span class="logo-mark" style="width:34px;height:34px"></span>
    <span class="logo-name" style="font-size:12px">CORVANTH VEYLOR</span>
  </div>
  <div class="abs line" style="left:0;right:0;top:236px">
    <svg width="12" height="12" viewBox="0 0 12 12"><path d="M2 1h3l1 3-2 1a7 7 0 003 3l1-2 3 1v3c-6 0-10-4-10-10z" fill="#fff"/></svg>1-888-888-8888</div>
  <div class="abs line" style="left:0;right:0;top:266px">
    <svg width="13" height="10" viewBox="0 0 13 10"><rect width="13" height="10" fill="#fff"/><path d="M0 0l6.5 5L13 0" fill="none" stroke="#000"/></svg>info@companyname.com</div>
  <p class="abs" style="left:0;right:0;top:334px;font-size:11px">© Corvanth Veylor. All Rights Reserved. | Privacy Policy</p>
</footer>

</body>
</html>
```